TLK Electricial Contracting Services

Hi guys, after a design for my small electrical company, have logo design files to be incorporated into the layout, the basic concept is electrical contracting services for residential, commercial, industrial & data services, image is clean clear and strong,

Card format is to have a nice clean logo on front,with maybe the Residential – commercial – industrial - data, followed with licensed & insured, followed by contact details on backside of the card.

Target Market(s)

Residential, commercial, industrial sectors.

Industry/Entity Type

Electrical

Contact Information for Business Card

TLK logo,
Residential – commercial – industrial - data
REC: 61307
Email: tlk@vornamail.net.au
Phone: 0487 352 019

Requirements
Must have
• Clean & strong design.
Nice to have
• If possible, I would like the logo colours inverted so the text is orange and the background is black on the front of the card, then the backside of the card be the reverse colour
Should not have
• No Sparks, lightning bolts,

```html
<!DOCTYPE html>
<html lang="en">
<head>
<meta charset="utf-8">
<title>TLK Electricial Contracting Services – Business Card</title>
<link href="https://fonts.googleapis.com/css2?family=Open+Sans:wght@400;600;700;800&display=swap" rel="stylesheet">
<style>
  :root {
    --orange: #f4822a;
    --black: #17161c;
    --white: #ffffff;
    --backdrop: #d9d9d9;
    --card-w: 620px;
    --card-h: 354px;
  }
  * { margin: 0; padding: 0; box-sizing: border-box; }
  html, body {
    width: 1200px; height: 900px; overflow: hidden;
    background: var(--backdrop);
    font-family: "Open Sans", Arial, sans-serif;
    color: var(--white);
  }
  .sheet {
    width: 1200px; height: 900px;
    display: flex; flex-direction: column; align-items: center; justify-content: center;
    gap: 60px;
  }
  .card {
    position: relative;
    width: var(--card-w); height: var(--card-h);
    overflow: hidden;
    box-shadow: 0 6px 18px rgba(0,0,0,0.18);
  }
  /* Front */
  .card-front { background: var(--orange); }
  .card-front .band-dark {
    position: absolute; left: 0; right: 0; top: 78px; height: 198px;
    background: var(--black);
  }
  .wordmark {
    position: absolute; text-align: right; line-height: 1;
  }
  .wordmark-initials {
    display: block; font-weight: 800; letter-spacing: 2px;
  }
  .wordmark-name {
    display: block; font-weight: 800; letter-spacing: 0.5px;
  }
  .card-front .wordmark { right: 150px; top: 108px; }
  .card-front .wordmark-initials { font-size: 98px; }
  .card-front .wordmark-name { font-size: 19px; margin-top: 6px; }

  /* Back */
  .card-back { background: var(--orange); }
  .card-back .band-top {
    position: absolute; left: 0; right: 0; top: 0; height: 158px; background: var(--black);
  }
  .card-back .band-bottom {
    position: absolute; left: 0; right: 0; bottom: 0; height: 26px; background: var(--black);
  }
  .card-back .wordmark { right: 48px; top: 26px; }
  .card-back .wordmark-initials { font-size: 88px; }
  .card-back .wordmark-name { font-size: 17px; margin-top: 6px; }

  .holder { position: absolute; left: 30px; top: 150px; }
  .holder-name { font-size: 22px; font-weight: 700; line-height: 1.2; }
  .holder-role { font-size: 13px; font-weight: 400; }

  .contact-list {
    position: absolute; right: 28px; bottom: 36px;
    list-style: none; text-align: right;
    font-size: 16px; line-height: 24px;
  }
  .contact-list li { display: flex; justify-content: flex-end; align-items: center; gap: 10px; white-space: nowrap; }
  .contact-list svg { width: 13px; height: 13px; fill: var(--white); flex: none; }
</style>
</head>
<body>
<main class="sheet">

  <section class="card card-front" aria-label="Card front">
    <div class="band-dark"></div>
    <div class="wordmark">
      <span class="wordmark-initials">TLK</span>
      <span class="wordmark-name">Tate Lowry Electrical</span>
    </div>
  </section>

  <section class="card card-back" aria-label="Card back">
    <div class="band-top"></div>
    <div class="band-bottom"></div>
    <div class="wordmark">
      <span class="wordmark-initials">TLK</span>
      <span class="wordmark-name">Tate Lowry Electrical</span>
    </div>
    <div class="holder">
      <p class="holder-name">Daniel Hartley</p>
      <p class="holder-role">Managing Director</p>
    </div>
    <ul class="contact-list">
      <li>123.456.7890
        <svg viewBox="0 0 16 16" aria-hidden="true"><path d="M2 5c0-2 2-3 6-3s6 1 6 3v1h-3V4.5H5V6H2zM4 7h8l2 6v1H2v-1zm4 2a2 2 0 100 4 2 2 0 000-4z"/></svg></li>
      <li>123.456.7890
        <svg viewBox="0 0 16 16" aria-hidden="true"><path d="M4 1h6l2 2v3H4zM2 7h12v6h-2v2H4v-2H2zm3 4v3h6v-3z"/></svg></li>
      <li>info@youremail.com
        <svg viewBox="0 0 16 16" aria-hidden="true"><path d="M1 3h14v10H1zm1.5 1.5L8 9l5.5-4.5z"/></svg></li>
      <li>www.website.com
        <svg viewBox="0 0 16 16" aria-hidden="true"><path d="M6.5 9.5l3-3 1 1-3 3zM4 9l-2 2a2.5 2.5 0 003.5 3.5l2-2-1-1-2 2a1 1 0 01-1.5-1.5l2-2zm8-2l2-2A2.5 2.5 0 0010.5 1.5l-2 2 1 1 2-2a1 1 0 011.5 1.5l-2 2z"/></svg></li>
      <li>1234, Address Goes Here, Country Name, 123456
        <svg viewBox="0 0 16 16" aria-hidden="true"><path d="M8 1a5 5 0 00-5 5c0 4 5 9 5 9s5-5 5-9a5 5 0 00-5-5zm0 3a2 2 0 110 4 2 2 0 010-4z"/></svg></li>
    </ul>
  </section>

</main>
</body>
</html>
```